Board to put on a meditation centre - Lantern Grove

I need a board design for a new meditation centre based in Oslo which offers free courses in meditation and self-empowerment. The size of the board is width 374cm x height 104cm.  The name of the meditation centre together with subtitles should be on the board but also some elegant decoration that matches the theme (lantern grove/meditation).
Here is the website of the meditation centre to give you a feeling of it: https://kvitfjellsenteret.no/
Good if you can use a blue color close to this one: rgb(37, 180, 193) as well as some brown/golden color (similar to the palette on the website).
On the board it should say:
Kveldens lund (in big letters, the rest is subtitles)
Meditasjon & Spirituell visdom
Kurs - Retreat - Dialog
kvitfjellsenteret.no
The design should be very elegant and beautiful and the feeling should be of "A Lantern Grove". A logo is here attached and should be used but I need to get a better quality version of it, will upload that as soon as possible.

```html
<!DOCTYPE html>
<html lang="no">
<head>
<meta charset="UTF-8">
<title>Kveldens lund – skilt</title>
<link rel="stylesheet" href="https://fonts.googleapis.com/css2?family=Playfair+Display:ital,wght@1,400&family=Montserrat:wght@500;600&display=swap">
<style>
  :root {
    --page-bg: #ffffff;
    --board-teal: #07b2c0;
    --ornament-light: #8fdfe5;
    --ornament-mid: #45c6d0;
    --line-white: rgba(255, 255, 255, 0.85);
    --title-brown: #3a1f15;
    --title-shadow: #0a8b96;
    --subtitle-white: #ffffff;
    --url-dark: #3a2a25;
    --mark-red: #d8262e;
  }
  html, body {
    margin: 0;
    padding: 0;
    width: 1200px;
    height: 632px;
    overflow: hidden;
    background: var(--page-bg);
  }
  .canvas {
    position: relative;
    width: 1200px;
    height: 632px;
  }
  .board {
    position: absolute;
    left: 53px;
    top: 166px;
    width: 1090px;
    height: 303px;
    background: var(--board-teal);
    overflow: hidden;
  }
  .ornament {
    position: absolute;
    top: 0;
    width: 190px;
    height: 303px;
  }
  .ornament--left {
    left: 0;
    background: radial-gradient(ellipse 190px 180px at 0% 50%, var(--ornament-light) 0%, var(--ornament-mid) 60%, var(--board-teal) 100%);
  }
  .ornament--right {
    right: 0;
    background: radial-gradient(ellipse 190px 180px at 100% 50%, var(--ornament-light) 0%, var(--ornament-mid) 60%, var(--board-teal) 100%);
  }
  .edge-curves {
    position: absolute;
    inset: 0;
    width: 1090px;
    height: 303px;
    pointer-events: none;
  }
  .edge-curves path {
    fill: none;
    stroke: var(--line-white);
    stroke-width: 2;
  }
  .edge-curves .thin {
    stroke-width: 1;
    stroke-dasharray: 2 5;
  }
  .board-title {
    position: absolute;
    left: 0;
    right: 0;
    top: 22px;
    margin: 0;
    text-align: center;
    font-family: "Playfair Display", serif;
    font-style: italic;
    font-weight: 400;
    font-size: 100px;
    line-height: 120px;
    color: var(--title-brown);
    text-shadow: 3px 3px 0 var(--title-shadow);
  }
  .subtitles {
    position: absolute;
    left: 0;
    right: 0;
    top: 157px;
    margin: 0;
    text-align: center;
    font-family: "Montserrat", sans-serif;
    font-weight: 600;
    font-size: 26px;
    line-height: 30px;
    color: var(--subtitle-white);
  }
  .subtitles span { display: block; }
  .site-link {
    position: absolute;
    left: 0;
    right: 0;
    top: 256px;
    display: flex;
    justify-content: center;
    align-items: center;
    gap: 8px;
    font-family: "Montserrat", sans-serif;
    font-weight: 500;
    font-size: 15px;
    color: var(--url-dark);
    text-decoration: none;
  }
  .site-link__dot {
    width: 24px;
    height: 24px;
    border-radius: 50%;
    background: var(--mark-red);
  }
</style>
</head>
<body>
  <div class="canvas">
    <section class="board">
      <div class="ornament ornament--left" role="img" aria-label="Dekorativ hvit mandala-ornamentikk langs venstre kant"></div>
      <div class="ornament ornament--right" role="img" aria-label="Dekorativ hvit mandala-ornamentikk langs høyre kant"></div>
      <svg class="edge-curves" viewBox="0 0 1090 303" aria-hidden="true">
        <path d="M0 8 C 150 40, 190 110, 190 151.5 C 190 193, 150 263, 0 295"/>
        <path class="thin" d="M0 24 C 120 55, 172 115, 172 151.5 C 172 188, 120 248, 0 279"/>
        <path d="M1090 8 C 940 40, 900 110, 900 151.5 C 900 193, 940 263, 1090 295"/>
        <path class="thin" d="M1090 24 C 970 55, 918 115, 918 151.5 C 918 188, 970 248, 1090 279"/>
      </svg>
      <h1 class="board-title">Kveldens lund</h1>
      <p class="subtitles">
        <span>Meditasjon &amp; Spirituell visdom</span>
        <span>Kurs - Retreat - Dialog</span>
      </p>
      <a class="site-link" href="https://kvitfjellsenteret.no/">
        <span class="site-link__dot"></span>
        <span>kvitfjellsenteret.no</span>
      </a>
    </section>
  </div>
</body>
</html>
```